Website Design for my Copper Distillation Equipment Business Nature Sciencey Theme

I already have a website www.cascobrewworks.com and its a sitevelo website builder one. But I cannot get the design right at all. I need this fixed.

I have logo. I need a redesign, for my website, the home page, that maybe I can have something similar in design- I can use as template to copy, for other pages so the whole thing matches? Look at my website so you understand I have a few pages...but most are links. Its a competition. Code has to be easy for me to implement, I am not expert.

Your advice needed..It would be a plus if I can update this myself throughout time. If I could have this explained to me too, the maintenance of it...how would I do this too..etc..pretend I am a child when you explain, if you can. I am not good with this stuff but I am smart and can learn fast.

I want a high end look. Maybe like an ivy league college-y look too, real preppy, chemistry...science-y, nature like is good, leaves, drops water, fields of wheat, lavender, etc.

I want every page to look similar, but the home page is what I want to be the main showpiece,..and I want each page have a little text section, maybe a photos section and a video section, for that market. Like a nice website. If I am not doing this right, let me know. I can work with you. Just help me, please. Let me know if I am doing this right.

When I pick my winning design, for my website, I will hire the artist one-on-one to re-design my shopping cart next. Or if I need additional help with implementing this current design, I can hire the same artist again too. I have a blog that I may want to hire the redesign as well too, but later on. My point is I am not just looking for one project here but I want to follow up with winning artist. So it would be return business for the winner.

I got my logo done here so I am repeat customer. And I have given that winning artist other design work.

Target Market(s)

Moonshine Stills I sell most, Essential Oil Business, Micro and Craft Distilleries, Canna-businesses, Alcohol Fuel

Industry/Entity Type

Business

Number of Pages Required

5+ page

Colors
ec1f27

Requirements
Must have
• The categories for the stills must be prominent and eye catching. The main photo I would like to be naturelike theme, but you can try out different things with me. I am open to ideas and suggestions. I would like this to be implemented easy and fast.
Nice to have
• My logo in it. You can use any of my photos as well from my pictoshare account. https://www.pictoshare.com/photos/81724596@K09/
• Colors of my Logo...matching design.
• Maybe some basic stock photos you see would match for me..
• Chemistry like symbols for the categories, I love that.

```html
<!DOCTYPE html>
<html lang="en">
<head>
<meta charset="utf-8">
<title>Casco Brew Works — Copper Reflux Stills</title>
<link href="https://fonts.googleapis.com/css2?family=Montserrat:wght@400;600;700&family=Open+Sans:wght@400;600&family=Ubuntu:wght@700&display=swap" rel="stylesheet">
<style>
:root{
  --ink:#2b2523;
  --text:#5c5654;
  --muted:#8a8482;
  --brand-brown:#574a46;
  --hero-light:#cfccc6;
  --hero-dark:#5f5a51;
  --title:#4a3731;
  --faint:#f1ecec;
  --collection-bg:#f6f6f6;
  --tile:#fcfcfc;
  --rule:#2b2523;
  --white:#ffffff;
}
*{margin:0;padding:0;box-sizing:border-box}
html,body{width:1200px;height:3482px;overflow:hidden;background:var(--white)}
body{position:relative;font-family:"Open Sans",Arial,sans-serif;color:var(--text)}
.abs{position:absolute}

/* hero */
.hero{left:0;top:0;width:1200px;height:668px;
  background:radial-gradient(ellipse at 30% 20%,rgba(255,255,255,.55),transparent 55%),
  linear-gradient(180deg,var(--hero-light) 0%,#a9a498 40%,#7f796d 70%,var(--hero-dark) 100%)}
.nav{top:55px;font-family:Montserrat,sans-serif;font-weight:700;font-size:9px;letter-spacing:1.3px;color:var(--ink);display:flex;gap:28px}
.nav--left{left:281px}
.nav--right{left:722px}
.brand-mark{left:555px;top:44px;width:90px;text-align:center;font-family:Montserrat,sans-serif;font-weight:700;font-size:22px;letter-spacing:1px;color:var(--ink)}
.hero-title{left:0;width:1200px;top:286px;text-align:center;font-family:Ubuntu,sans-serif;font-weight:700;font-size:58px;letter-spacing:1px;color:var(--title);text-shadow:2px 3px 4px rgba(0,0,0,.35)}
.hero-sub{left:0;width:1200px;top:366px;text-align:center;font-family:Ubuntu,sans-serif;font-weight:700;font-size:22px;color:var(--title);text-shadow:1px 2px 3px rgba(0,0,0,.3)}

/* intro */
.intro-deco{left:400px;top:740px;width:400px;text-align:center;font-family:Montserrat,sans-serif;font-weight:700;font-size:300px;line-height:340px;color:var(--faint)}
.intro-heading{left:0;width:1200px;top:807px;text-align:center;font-family:Montserrat,sans-serif;font-weight:700;font-size:15px;letter-spacing:2.2px;color:var(--ink)}
.intro-text{left:285px;width:630px;top:868px;text-align:center;font-size:15px;line-height:24px;color:var(--text)}

/* posts */
.photo{background:linear-gradient(135deg,#8a847e,#4b4642)}
.post-date{font-size:9px;color:var(--muted)}
.post-title{font-family:Montserrat,sans-serif;font-weight:700;font-size:17px;letter-spacing:1px;color:var(--ink);line-height:22px}
.post-rule{height:2px;width:60px;background:var(--rule)}
.post-body{font-size:10px;line-height:16px;color:var(--text);width:240px}
.post-body p{margin-bottom:12px}
.btn{width:93px;height:28px;border:1.5px solid var(--ink);font-family:Montserrat,sans-serif;font-size:9px;font-weight:600;letter-spacing:1px;color:var(--ink);display:flex;align-items:center;justify-content:center}
.right{text-align:right}

/* gallery */
.gallery-heading{left:0;width:1200px;top:2116px;text-align:center;font-family:Montserrat,sans-serif;font-size:11px;font-weight:600;letter-spacing:1.5px;color:var(--ink)}
.gallery{left:0;top:2159px;width:1200px;height:199px;display:flex}
.gallery div{flex:1}

/* collection */
.collection{left:0;top:2358px;width:1200px;height:752px;background:var(--collection-bg)}
.collection-title{left:0;width:1200px;top:2416px;text-align:center;font-family:Montserrat,sans-serif;font-weight:700;font-size:20px;letter-spacing:2.5px;color:var(--ink)}
.collection-sub{left:0;width:1200px;top:2444px;text-align:center;font-family:Montserrat,sans-serif;font-size:10px;letter-spacing:1.5px;color:var(--muted)}
.product{background:radial-gradient(ellipse at 50% 60%,#d9d2cb 0%,#f3f1ef 45%,var(--tile) 70%)}
.product-divider{left:831px;top:2781px;width:1px;height:236px;background:#d4d0ce}

/* newsletter */
.signup-label{left:304px;top:3185px;font-family:Montserrat,sans-serif;font-weight:700;font-size:10px;letter-spacing:1.3px;color:var(--ink)}
.signup-input{left:592px;top:3168px;width:329px;height:37px;border:1.5px solid #9a9391;display:flex;align-items:center;justify-content:center;font-size:15px;color:#b0aaa8}
.signup-note{left:592px;top:3214px;font-size:9px;color:var(--muted)}

/* footer */
.footer{left:0;top:3303px;width:1200px;height:179px;background:var(--brand-brown)}
.footer-links{left:232px;top:3366px;display:flex;gap:22px;font-size:9px;color:#eae4e2}
.footer-mark{left:540px;top:3375px;width:120px;text-align:center;font-family:Montserrat,sans-serif;font-weight:700;font-size:28px;color:var(--white)}
.cards{left:720px;top:3360px;display:flex;gap:10px}
.card{width:42px;height:26px;background:var(--white);border-radius:2px;display:flex;align-items:center;justify-content:center;font-family:Montserrat,sans-serif;font-weight:600;font-size:7px;color:var(--ink)}
</style>
</head>
<body>

<section class="abs hero" role="img" aria-label="Misty photograph of tall wild grass in a sunlit field"></section>
<nav class="abs nav nav--left"><span>COLLECTION</span><span>HISTORY</span><span>NEWS</span></nav>
<div class="abs brand-mark">CASCO</div>
<nav class="abs nav nav--right"><span>SHOP</span><span>ABOUT ME</span><span>CONTACT</span></nav>
<h1 class="abs hero-title">CASCO BREW WORKS</h1>
<p class="abs hero-sub">We make the best Copper Moonshine Alcohol Reflux Stills</p>

<div class="abs intro-deco" aria-hidden="true">CB</div>
<h2 class="abs intro-heading">I SPECIALIZE IN DISTILLATION OF EVERYTHING</h2>
<p class="abs intro-text">Quisque pretium nulla nec risus laoreet, eu vestibulum magna pellentesque. Nullam ornare pulvinar consequat. Vestibulum suscipit purus a quam egestas, ac congue risus feugiat. Aenean sagittis ultricies tincidunt. Nam ante nibh, euismod id cursus sit amet, ornare at ligula.</p>

<!-- post one -->
<div class="abs photo" style="left:297px;top:1137px;width:330px;height:218px" role="img" aria-label="Workshop with steel distilling kegs and two workers"></div>
<div class="abs photo" style="left:248px;top:1342px;width:235px;height:155px;background:linear-gradient(135deg,#9c958e,#55504b)" role="img" aria-label="Row of stainless steel still kegs on a workshop floor"></div>
<p class="abs post-date" style="left:671px;top:1198px">03 OCTOBER 2014</p>
<h3 class="abs post-title" style="left:671px;top:1218px">DISTILL ANYTHING!</h3>
<div class="abs post-rule" style="left:671px;top:1284px"></div>
<div class="abs post-body" style="left:671px;top:1242px">
  <p>Aenean eros ex, elementum eu enim quis, lacinia ornare tellus. Ut mattis, risus quis commodo molestie, purus dui rhoncus ex, eu efficitur ligula enim sit amet tortor. Quisque in lobortis lorem.</p>
  <p>Pellentesque habitant morbi tristique senectus et netus et malesuada fames ac turpis egestas. Fusce suscipit feugiat quam, eu posuere tellus scelerisque a.</p>
  <p>Donec aliquam, lacus nec euismod elementum.</p>
</div>
<div class="abs btn" style="left:671px;top:1444px">READ MORE</div>

<!-- post two -->
<p class="abs post-date right" style="left:338px;width:200px;top:1596px">08 MARCH 2014</p>
<h3 class="abs post-title right" style="left:318px;width:220px;top:1612px">MAKE LOVELY OILS<br>FOR THE LADY.</h3>
<div class="abs post-rule" style="left:478px;top:1685px"></div>
<div class="abs post-body right" style="left:298px;top:1700px">
  <p>Aenean eros ex, elementum eu enim quis, lacinia ornare tellus. Ut mattis, risus quis commodo molestie, purus dui rhoncus ex, eu efficitur ligula enim sit amet tortor. Quisque in lobortis lorem.</p>
  <p>Pellentesque habitant morbi tristique senectus et netus et malesuada fames ac turpis egestas. Fusce suscipit feugiat quam, eu posuere tellus scelerisque a.</p>
  <p>Donec aliquam, lacus nec euismod elementum.</p>
</div>
<div class="abs btn" style="left:445px;top:1906px">READ MORE</div>
<div class="abs photo" style="left:812px;top:1643px;width:112px;height:344px;background:linear-gradient(180deg,#c9c6c2,#5b5753)" role="img" aria-label="Tall glass collection jars in a row"></div>
<div class="abs photo" style="left:580px;top:1602px;width:232px;height:348px;background:linear-gradient(180deg,#4f5a45,#8d7e86 70%,#6f6470)" role="img" aria-label="Woman smelling a lavender sprig in a garden"></div>

<!-- gallery -->
<h2 class="abs gallery-heading">CASCO BREW WORKS PICTOSHARE</h2>
<div class="abs gallery">
  <div style="background:linear-gradient(135deg,#6b5a4a,#3e342c)" role="img" aria-label="Glass of clear spirit being poured"></div>
  <div style="background:linear-gradient(135deg,#8a7d6d,#4a4138)" role="img" aria-label="Dried herbs in a wooden bucket"></div>
  <div style="background:linear-gradient(135deg,#6e7a5a,#3f4a33)" role="img" aria-label="Man standing beside a keg still outdoors"></div>
  <div style="background:linear-gradient(135deg,#a48a6e,#4c3d30)" role="img" aria-label="Close-up of copper still fittings"></div>
  <div style="background:linear-gradient(135deg,#7c7b72,#3c3b36)" role="img" aria-label="Man in a cap working outdoors"></div>
  <div style="background:linear-gradient(135deg,#8a5a44,#3d2a22)" role="img" aria-label="Hands working on copper tubing"></div>
</div>

<!-- collection -->
<section class="abs collection"></section>
<h2 class="abs collection-title">2014 COLLECTION</h2>
<p class="abs collection-sub">NOW AVAILABLE</p>
<div class="abs product" style="left:228px;top:2495px;width:206px;height:267px" role="img" aria-label="Copper reflux column mounted on a steel keg"></div>
<div class="abs product" style="left:499px;top:2495px;width:209px;height:267px" role="img" aria-label="Copper pot still column on a brass stand"></div>
<div class="abs product" style="left:766px;top:2495px;width:204px;height:267px" role="img" aria-label="Copper reflux column with coil on a steel keg"></div>
<div class="abs product" style="left:297px;top:2781px;width:302px;height:236px" role="img" aria-label="Two amber essential oil bottles with dried rosebuds"></div>
<div class="abs product" style="left:622px;top:2781px;width:207px;height:236px" role="img" aria-label="Clear swing-top glass bottle"></div>
<div class="abs product-divider"></div>

<!-- newsletter -->
<p class="abs signup-label">STAY CONNECTED TO CASCO BREW WORKS</p>
<div class="abs signup-input">Your Email Address</div>
<p class="abs signup-note">Get the latest product info, updates, special offers and much more.</p>

<!-- footer -->
<footer class="abs footer"></footer>
<nav class="abs footer-links"><span>Disclaimer</span><span>Terms &amp; Conditions</span><span>Privacy policy</span></nav>
<div class="abs footer-mark">CASCO</div>
<div class="abs cards">
  <span class="card">VANTRA</span><span class="card">PAYLOW</span><span class="card">MINTCARD</span><span class="card">DYSCOVO</span><span class="card">AMBLO</span>
</div>

</body>
</html>
```